skin care company
skin care company - Personal Care
Creative Brief
Simple
Lorena Quastelli
General Manager
Morvel Trade Plaza 14th Floor Harbin Crescent Road Dubai, UAE
lquastelli@velmoraskin.com
For letter head please use info@velmoraskin.com
bghamdi bghamdi
for b.card both sides need to be black. also add this salgon under the logo in b.card Where Skin Meets Nature
letterhead sample attached.
Attached.
RAS518 RAS518
hi bghamdi did you not attach your logo?
For business card. Contact information on side and logo in back side.
B.card: add icon for mobile and for work phone. letterhead: in the footer put public email info@velmoraskin.com work phone: +97143918402 and address in one line. also there is missing stationary such as envelop.

```html
<!DOCTYPE html>
<html lang="en">
<head>
<meta charset="utf-8">
<title>Velmora Stationery</title>
<link href="https://fonts.googleapis.com/css2?family=Montserrat:wght@300;400;600;700&display=swap" rel="stylesheet">
<style>
:root{
  --backdrop:#8b8b8b;
  --paper:#ffffff;
  --green:#8dc63f;
  --dark:#3b3b3b;
  --black:#161616;
  --ink:#4a4a4a;
  --ink-light:#d6d6d6;
}
*{margin:0;padding:0;box-sizing:border-box}
html,body{width:1200px;height:600px;overflow:hidden}
body{background:var(--backdrop);font-family:'Montserrat',sans-serif;color:var(--ink);position:relative}
.sheet{position:absolute;background:var(--paper);overflow:hidden}
.brand{font-family:'Montserrat',sans-serif;font-weight:300;color:var(--green);letter-spacing:4px;position:absolute;white-space:nowrap}
.edge-band{position:absolute;left:0;bottom:0;width:100%;display:block}
.contact-row{position:absolute;display:flex;align-items:flex-start;gap:18px;font-size:6px;line-height:8px}
.contact-item{display:flex;align-items:flex-start;gap:4px}
.icon{width:8px;height:8px;flex:none;fill:var(--ink)}

/* envelope */
.envelope-front{left:62px;top:103px;width:432px;height:190px}
.envelope-front .brand{left:30px;top:18px;font-size:24px}
.envelope-front .contact-row{left:30px;top:145px;width:380px}
.envelope-front .address{margin-left:auto}
.envelope-flap{left:62px;top:293px;width:432px;height:201px}

/* letterhead */
.letterhead{left:511px;top:103px;width:279px;height:391px}
.letterhead .brand{right:18px;top:34px;font-size:22px}
.letterhead .contact-row{left:18px;top:351px;gap:10px;font-size:5px;line-height:6px}
.letterhead .icon{width:6px;height:6px}

/* business card */
.card-front{left:806px;top:103px;width:329px;height:190px;background:var(--black)}
.card-name{position:absolute;right:22px;top:22px;text-align:right}
.card-name h1{font-size:17px;font-weight:700;color:var(--paper);letter-spacing:1px}
.card-name p{font-size:6px;letter-spacing:1.5px;text-transform:uppercase;margin-top:3px;color:var(--green)}
.card-contacts{position:absolute;left:22px;top:74px;list-style:none;font-size:7px;line-height:9px;color:var(--ink-light)}
.card-contacts li{display:flex;align-items:flex-start;gap:6px;margin-bottom:7px}
.card-contacts .icon{fill:var(--green)}
.card-back{left:806px;top:307px;width:329px;height:187px;background:var(--black)}
.card-lockup{position:absolute;left:0;right:0;top:50%;transform:translateY(-50%);text-align:center}
.card-lockup .brand{position:static;display:block;font-size:30px;letter-spacing:5px}
.card-lockup .slogan{display:block;margin-top:8px;font-size:8px;font-weight:400;letter-spacing:2px;text-transform:uppercase;color:var(--ink-light)}
</style>
</head>
<body>

<!-- envelope front -->
<section class="sheet envelope-front">
  <div class="brand">VELMORA</div>
  <div class="contact-row">
    <span class="contact-item"><svg class="icon" viewBox="0 0 10 10"><rect x="0" y="2" width="10" height="6" rx="1"/><path d="M0 2.5L5 6L10 2.5" stroke="#fff" stroke-width="1" fill="none"/></svg>info@velmoraskin.com</span>
    <span class="contact-item"><svg class="icon" viewBox="0 0 10 10"><path d="M2 0.5h2l1 2.5-1.3 1a6 6 0 0 0 2.3 2.3l1-1.3 2.5 1v2a1 1 0 0 1-1 1A8.5 8.5 0 0 1 1 1.5a1 1 0 0 1 1-1z"/></svg>+97143918402</span>
    <span class="contact-item address"><svg class="icon" viewBox="0 0 10 10"><path d="M5 0a3.5 3.5 0 0 0-3.5 3.5C1.5 6 5 10 5 10s3.5-4 3.5-6.5A3.5 3.5 0 0 0 5 0zm0 5a1.5 1.5 0 1 1 0-3 1.5 1.5 0 0 1 0 3z"/></svg>Morvel Trade Plaza<br>14th Floor<br>Harbin Crescent Road<br>Dubai, UAE</span>
  </div>
  <svg class="edge-band" width="432" height="12" viewBox="0 0 432 12" preserveAspectRatio="none">
    <polygon points="0,2 400,2 410,12 0,12" fill="var(--green)"/>
    <polygon points="390,0 432,0 432,12 402,12" fill="var(--dark)"/>
  </svg>
</section>

<!-- envelope flap -->
<section class="sheet envelope-flap">
  <svg width="432" height="201" viewBox="0 0 432 201">
    <path d="M0 8H432V44H0Z" fill="var(--green)"/>
    <path d="M0 44Q0 62 20 62V44Z" fill="var(--green)"/>
    <path d="M432 44Q432 62 412 62V44Z" fill="var(--green)"/>
  </svg>
</section>

<!-- letterhead -->
<section class="sheet letterhead">
  <div class="brand">VELMORA</div>
  <div class="contact-row">
    <span class="contact-item"><svg class="icon" viewBox="0 0 10 10"><rect x="0" y="2" width="10" height="6" rx="1"/><path d="M0 2.5L5 6L10 2.5" stroke="#fff" stroke-width="1" fill="none"/></svg>info@velmoraskin.com</span>
    <span class="contact-item"><svg class="icon" viewBox="0 0 10 10"><path d="M2 0.5h2l1 2.5-1.3 1a6 6 0 0 0 2.3 2.3l1-1.3 2.5 1v2a1 1 0 0 1-1 1A8.5 8.5 0 0 1 1 1.5a1 1 0 0 1 1-1z"/></svg>+97143918402</span>
    <span class="contact-item"><svg class="icon" viewBox="0 0 10 10"><path d="M5 0a3.5 3.5 0 0 0-3.5 3.5C1.5 6 5 10 5 10s3.5-4 3.5-6.5A3.5 3.5 0 0 0 5 0zm0 5a1.5 1.5 0 1 1 0-3 1.5 1.5 0 0 1 0 3z"/></svg>Morvel Trade Plaza 14th Floor<br>Harbin Crescent Road<br>Dubai, UAE</span>
  </div>
  <svg class="edge-band" width="279" height="8" viewBox="0 0 279 8" preserveAspectRatio="none">
    <polygon points="0,0 180,0 188,8 0,8" fill="var(--green)"/>
    <polygon points="182,0 279,0 279,8 190,8" fill="var(--dark)"/>
  </svg>
</section>

<!-- business card front -->
<section class="sheet card-front">
  <div class="card-name">
    <h1>LORENA QUASTELLI</h1>
    <p>General Manager</p>
  </div>
  <ul class="card-contacts">
    <li><svg class="icon" viewBox="0 0 10 10"><path d="M5 0a3.5 3.5 0 0 0-3.5 3.5C1.5 6 5 10 5 10s3.5-4 3.5-6.5A3.5 3.5 0 0 0 5 0zm0 5a1.5 1.5 0 1 1 0-3 1.5 1.5 0 0 1 0 3z"/></svg><span>Morvel Trade Plaza 14th Floor<br>Harbin Crescent Road<br>Dubai, UAE</span></li>
    <li><svg class="icon" viewBox="0 0 10 10"><path d="M2 0.5h2l1 2.5-1.3 1a6 6 0 0 0 2.3 2.3l1-1.3 2.5 1v2a1 1 0 0 1-1 1A8.5 8.5 0 0 1 1 1.5a1 1 0 0 1 1-1z"/></svg>+97143918402</li>
    <li><svg class="icon" viewBox="0 0 10 10"><rect x="2.5" y="0" width="5" height="10" rx="1"/><rect x="3.5" y="1.2" width="3" height="6" fill="#161616"/></svg>+971504471208</li>
    <li><svg class="icon" viewBox="0 0 10 10"><rect x="0" y="2" width="10" height="6" rx="1"/><path d="M0 2.5L5 6L10 2.5" stroke="#161616" stroke-width="1" fill="none"/></svg>lquastelli@velmoraskin.com</li>
  </ul>
  <svg class="edge-band" width="329" height="10" viewBox="0 0 329 10" preserveAspectRatio="none">
    <polygon points="0,0 272,0 280,10 0,10" fill="var(--green)"/>
    <polygon points="274,0 329,0 329,10 282,10" fill="var(--dark)"/>
  </svg>
</section>

<!-- business card back -->
<section class="sheet card-back">
  <div class="card-lockup">
    <span class="brand">VELMORA</span>
    <span class="slogan">Where Skin Meets Nature</span>
  </div>
</section>

</body>
</html>
```